Heritage Hollow Business Cards

Require a business card design. <br/><br/>Needs to include logo (either round or long version) plus these details:<br/>Maya Torvell<br/>Heritage Hollow<br/>maya@kelvadtrading.com.au<br/>02 6481 7395<br/>PO Box Glenwarra NSW 2791<br/>www.heritagehollow.com.au<br/><br/>I need in an editable format so that I can create for multiple staff members. <br/><br/>

Target Market(s)

We are an online store selling renovation products to home owners are builders. Looking for a classic classy design.

Industry/Entity Type

Home And Garden

Contact Information for Business Card

Maya Torvell
Heritage Hollow
maya@kelvadtrading.com.au
02 6481 7395
PO Box Glenwarra NSW 2791
www.heritagehollow.com.au

Colors

Designer to choose colors to be used in the design.

Requirements
Must have
• Must include Logo.

```html
<!DOCTYPE html>
<html lang="en">
<head>
<meta charset="utf-8">
<title>Heritage Hollow Business Cards</title>
<link href="https://fonts.googleapis.com/css2?family=Tinos:wght@400;700&display=swap" rel="stylesheet">
<style>
  :root {
    --backdrop: #d8d2c7;
    --card-white: #f4f4f4;
    --card-grey: #c9c9c9;
    --card-mid: #a9a9a9;
    --card-black: #262324;
    --ink-dark: #3a3a3a;
    --ink-light: #f2f2f2;
    --ink-soft: #d9d9d9;
  }
  * { margin: 0; padding: 0; box-sizing: border-box; }
  html, body {
    width: 1200px;
    height: 780px;
    overflow: hidden;
  }
  body {
    background: var(--backdrop);
    font-family: "Tinos", "Times New Roman", serif;
    display: flex;
    align-items: center;
    justify-content: center;
    gap: 40px;
  }
  .card {
    position: relative;
    width: 520px;
    height: 318px;
    border-radius: 3px;
    overflow: hidden;
    box-shadow: 0 10px 24px rgba(0, 0, 0, 0.25);
  }
  .card-front { background: var(--card-white); }
  .card-back {
    background: radial-gradient(ellipse at 45% 40%, #333031 0%, var(--card-black) 70%);
  }
  .front-shapes {
    position: absolute;
    inset: 0;
    width: 100%;
    height: 100%;
  }
  .brand {
    position: absolute;
    display: flex;
    align-items: center;
    gap: 12px;
    white-space: nowrap;
  }
  .brand-mark {
    width: 26px;
    height: 26px;
    border-radius: 50%;
    border: 2px solid currentColor;
    flex: none;
  }
  .brand-name {
    font-weight: 400;
    letter-spacing: 0.5px;
  }
  .card-front .brand {
    left: 30px;
    top: 138px;
    color: var(--ink-dark);
  }
  .card-front .brand-name { font-size: 30px; }
  .card-back .brand {
    left: 50%;
    top: 50%;
    transform: translate(-50%, -50%);
    color: var(--ink-light);
  }
  .card-back .brand-name { font-size: 40px; }
  .card-back .brand-mark { width: 34px; height: 34px; }
  .contact {
    position: absolute;
    right: 22px;
    top: 34px;
    color: var(--ink-light);
    text-align: right;
  }
  .contact-name {
    font-size: 24px;
    line-height: 1.1;
  }
  .contact-role {
    font-size: 12px;
    color: var(--ink-soft);
    margin-bottom: 16px;
  }
  .contact-list { list-style: none; }
  .contact-list li {
    display: flex;
    align-items: center;
    justify-content: flex-end;
    gap: 8px;
    font-size: 12px;
    line-height: 1;
    margin-bottom: 9px;
  }
  .contact-icon {
    width: 14px;
    height: 14px;
    flex: none;
  }
</style>
</head>
<body>

  <section class="card card-front" aria-label="Business card front">
    <svg class="front-shapes" viewBox="0 0 520 318" preserveAspectRatio="none" aria-hidden="true">
      <path d="M222 0 C300 80 330 200 332 318 L520 318 L520 0 Z" fill="var(--card-grey)"/>
      <path d="M236 0 C312 80 342 200 346 318 L520 318 L520 0 Z" fill="var(--card-mid)"/>
      <path d="M250 0 C326 80 356 200 362 318 L520 318 L520 0 Z" fill="var(--card-black)"/>
    </svg>

    <div class="brand">
      <span class="brand-mark"></span>
      <span class="brand-name">Heritage Hollow</span>
    </div>

    <div class="contact">
      <p class="contact-name">Maya Torvell</p>
      <p class="contact-role">Managing Director</p>
      <ul class="contact-list">
        <li>02 6481 7395
          <svg class="contact-icon" viewBox="0 0 14 14" aria-hidden="true">
            <circle cx="7" cy="7" r="6.3" fill="none" stroke="currentColor" stroke-width="1"/>
            <path d="M4.6 3.8 L5.8 3.6 L6.4 5.2 L5.7 5.8 C6.1 6.8 6.9 7.6 7.9 8.1 L8.5 7.4 L10.1 8 L9.9 9.2 C7 9.4 4.4 6.8 4.6 3.8 Z" fill="currentColor"/>
          </svg>
        </li>
        <li>maya@kelvadtrading.com.au
          <svg class="contact-icon" viewBox="0 0 14 14" aria-hidden="true">
            <circle cx="7" cy="7" r="6.3" fill="none" stroke="currentColor" stroke-width="1"/>
            <rect x="3.8" y="4.8" width="6.4" height="4.4" fill="none" stroke="currentColor" stroke-width="0.9"/>
            <path d="M3.8 4.8 L7 7.3 L10.2 4.8" fill="none" stroke="currentColor" stroke-width="0.9"/>
          </svg>
        </li>
        <li>PO Box Glenwarra NSW 2791
          <svg class="contact-icon" viewBox="0 0 14 14" aria-hidden="true">
            <circle cx="7" cy="7" r="6.3" fill="none" stroke="currentColor" stroke-width="1"/>
            <path d="M7 10.6 C5.4 8.6 4.6 7.3 4.6 6 A2.4 2.4 0 0 1 9.4 6 C9.4 7.3 8.6 8.6 7 10.6 Z" fill="currentColor"/>
            <circle cx="7" cy="6" r="0.9" fill="var(--card-black)"/>
          </svg>
        </li>
        <li>www.heritagehollow.com.au
          <svg class="contact-icon" viewBox="0 0 14 14" aria-hidden="true">
            <circle cx="7" cy="7" r="6.3" fill="none" stroke="currentColor" stroke-width="1"/>
            <circle cx="7" cy="7" r="3.4" fill="none" stroke="currentColor" stroke-width="0.8"/>
            <ellipse cx="7" cy="7" rx="1.4" ry="3.4" fill="none" stroke="currentColor" stroke-width="0.7"/>
            <path d="M3.6 7 H10.4" stroke="currentColor" stroke-width="0.7"/>
          </svg>
        </li>
      </ul>
    </div>
  </section>

  <section class="card card-back" aria-label="Business card back">
    <div class="brand">
      <span class="brand-mark"></span>
      <span class="brand-name">Heritage Hollow</span>
    </div>
  </section>

</body>
</html>
```